Business Card Design

I already have a company logo for my company. I have a logo for the manufacturer we represent. I want a professional business card design.

```html
<!DOCTYPE html>
<html lang="en">
<head>
<meta charset="UTF-8">
<title>Beacon Alert Group – Business Card</title>
<link href="https://fonts.googleapis.com/css2?family=Open+Sans:wght@400;600;700&display=swap" rel="stylesheet">
<style>
  :root {
    --stage: #222222;
    --card-dark: #1c1c1e;
    --brand-red: #e11f26;
    --brand-orange: #f07a3a;
    --brand-gold: #d4a12a;
    --ink-light: #f2f2f2;
    --divider: #8a8a8a;
  }
  * { box-sizing: border-box; margin: 0; padding: 0; }
  html, body {
    width: 1200px; height: 780px; overflow: hidden;
    background: var(--stage);
    font-family: "Open Sans", Arial, sans-serif;
  }
  .sheet {
    width: 1200px; height: 780px;
    display: flex; align-items: center; justify-content: center; gap: 50px;
  }
  .card {
    position: relative;
    width: 540px; height: 308px;
    border-radius: 22px;
    overflow: hidden;
    box-shadow: 0 14px 30px rgba(0,0,0,.45);
  }
  /* Front */
  .card-front { background: var(--card-dark); color: var(--ink-light); }
  .brand {
    position: absolute; left: 40px; top: 62px;
    display: flex; align-items: center; gap: 12px;
  }
  .brand-mark { width: 22px; height: 22px; background: var(--brand-red); }
  .brand-name {
    font-weight: 700; font-size: 20px; line-height: 1.1;
    color: var(--ink-light); letter-spacing: .5px; text-transform: uppercase;
  }
  .divider {
    position: absolute; left: 262px; top: 68px;
    width: 1px; height: 150px; background: var(--divider);
  }
  .person { position: absolute; left: 288px; top: 62px; }
  .person-name { font-weight: 700; font-size: 29px; line-height: 1.1; }
  .person-name .first { color: var(--brand-red); }
  .person-name .last { color: var(--brand-gold); }
  .person-title { font-size: 15px; margin-top: 4px; color: var(--ink-light); }
  .contacts { list-style: none; margin-top: 18px; }
  .contacts li {
    display: flex; align-items: center; gap: 9px;
    font-size: 15px; line-height: 24px;
  }
  .contacts svg { width: 14px; height: 14px; flex: none; }
  .address {
    position: absolute; left: 40px; bottom: 34px;
    font-size: 14px; color: var(--ink-light);
  }
  /* Back */
  .card-back { background: var(--brand-red); }
  .back-pattern {
    position: absolute; inset: 0;
    background: linear-gradient(200deg, var(--brand-orange) 0%, #e8502e 30%, var(--brand-red) 60%);
  }
  .back-brand {
    position: absolute; right: 70px; bottom: 46px;
    display: flex; align-items: center; gap: 6px;
  }
  .back-brand .brand-mark { width: 10px; height: 10px; background: var(--ink-light); }
  .back-brand .brand-name { font-size: 10px; }
</style>
</head>
<body>
<main class="sheet">
  <section class="card card-front" aria-label="Business card front">
    <div class="brand">
      <span class="brand-mark"></span>
      <span class="brand-name">Beacon Alert<br>Group LLC</span>
    </div>
    <div class="divider"></div>
    <div class="person">
      <h1 class="person-name"><span class="first">Daniel</span> <span class="last">Kerova</span></h1>
      <p class="person-title">Managing Director</p>
      <ul class="contacts">
        <li>
          <svg viewBox="0 0 24 24" aria-hidden="true"><path fill="var(--brand-red)" d="M6.6 10.8a15 15 0 0 0 6.6 6.6l2.2-2.2c.3-.3.7-.4 1-.2 1.1.4 2.3.6 3.6.6.6 0 1 .4 1 1V20c0 .6-.4 1-1 1A17 17 0 0 1 3 4c0-.6.4-1 1-1h3.5c.6 0 1 .4 1 1 0 1.3.2 2.5.6 3.6.1.3 0 .7-.2 1z"/></svg>
          (555) 214-3086
        </li>
        <li>
          <svg viewBox="0 0 24 24" aria-hidden="true"><rect x="2" y="5" width="20" height="14" rx="2" fill="var(--brand-red)"/><path d="M3 6l9 7 9-7" stroke="var(--card-dark)" stroke-width="2" fill="none"/></svg>
          info@website.com
        </li>
        <li>
          <svg viewBox="0 0 24 24" aria-hidden="true"><circle cx="12" cy="12" r="10" fill="var(--brand-red)"/><path d="M2 12h20M12 2c3 3 3 17 0 20M12 2c-3 3-3 17 0 20" stroke="var(--card-dark)" stroke-width="1.5" fill="none"/></svg>
          www.website.com
        </li>
      </ul>
    </div>
    <p class="address">1840 Meadow Ln. Suite 310 Riverton, TX 75010</p>
  </section>

  <section class="card card-back" aria-label="Business card back">
    <div class="back-pattern" role="img" aria-label="Repeating chevron pattern in red and orange"></div>
    <div class="back-brand">
      <span class="brand-mark"></span>
      <span class="brand-name">Beacon Alert</span>
    </div>
  </section>
</main>
</body>
</html>
```